Brovan - Web Design Rebrand for Manufacturing Automation Company

I need a new brand for a customer based in Ireland.
The website currently: https://corvethsystems.example/
Corveth Systems provides a wide range of automation and IT solutions used in manufacturing operations.
Their solutions span a broad spectrum of technology from physical machines and robots to cloud based management solutions for these systems.
They are an Authorised Distributor for Pelmont Controls.
Their partnership with Pelmont Controls will now include working closely to keep track of supply trends and preparing customers for future Data Centre projects.

Essentially their USP:
They have a large team of specialist technical people spanning the breadth of skills to be able to deploy and support automation and IT solutions in manufacturing in the Life Sciences Industry.

Along with Pelmont Controls, they have specialist teams for accelerating Data Center applications.

Competitor websites:
https://www.duravex.example/global/en.html - I really like the layout of their partnerships/collaborations section.
https://global.qtl.example/group/en - Their first moving imagery/tagline and 'discover more' when you enter the site is really eye-catching.
https://www.kv.example/uk/en/ - They layout and structure of the 'The core of what we do section' is really nice.

These are a big companies so anything we could steal would be good 😊

They want:
• Fresh, sharp imagery
• Movement on the main page and perhaps video on some sections? - similar to QTL
• A page to showcase Automation Solutions
• A page to showcase Data Centers
• About us
• Sectors they operate in (includes Life Sciences, Food & Bev, Data Centres)

Industry/Entity Type

Life Science Manufacturing

Number of Pages Required

1 page

Font styles to use
Sans Serif

Colors
0054AA
0677BA
7BADD7
CADEEF
E8F1F8

Requirements
Must have
• Moving Imagery

```html
<!DOCTYPE html>
<html lang="en">
<head>
<meta charset="utf-8">
<title>Corveth Systems</title>
<link href="https://fonts.googleapis.com/css2?family=Syncopate:wght@400;700&family=Poppins:wght@400;500;600;700&display=swap" rel="stylesheet">
<style>
:root{
  --navy:#0b1630;
  --ink:#0d1b3e;
  --accent:#1aa3e8;
  --blue-deep:#0054aa;
  --blue:#0677ba;
  --blue-soft:#7badd7;
  --blue-pale:#cadeef;
  --blue-mist:#e8f1f8;
  --text:#2b2f3a;
  --muted:#555b66;
  --white:#ffffff;
}
*{box-sizing:border-box;margin:0;padding:0}
html,body{width:1200px;height:3213px;overflow:hidden}
body{position:relative;background:var(--white);font-family:"Poppins",sans-serif;color:var(--text)}
.abs{position:absolute}
.display{font-family:"Syncopate",sans-serif;font-weight:700;color:var(--ink);letter-spacing:3px;text-transform:uppercase}
.btn{position:absolute;display:flex;align-items:center;justify-content:center;background:var(--accent);color:var(--white);font-size:11px;font-weight:700;text-transform:uppercase;border-radius:2px}

/* hero */
.hero{left:0;top:0;width:1200px;height:690px;background:radial-gradient(ellipse 60% 55% at 70% 70%,#1b4f86 0%,#0d2a55 40%,#07112b 80%);}
.hero-glow{left:0;top:380px;width:1200px;height:310px;background:linear-gradient(180deg,rgba(11,22,48,0) 0%,rgba(30,100,170,.55) 60%,rgba(40,120,190,.35) 100%)}
.brand{left:144px;top:31px;display:flex;align-items:center}
.brand-name{font-size:17px;line-height:24px;font-weight:600;letter-spacing:1px;color:var(--accent);text-transform:uppercase;white-space:nowrap}
.nav{top:36px;left:545px;display:flex;gap:27px;font-size:14px;line-height:20px;color:var(--white);text-transform:uppercase;font-weight:400;white-space:nowrap}
.social{left:1026px;top:30px;width:30px;height:30px;border-radius:50%;background:var(--accent)}
.header-rule{left:144px;top:91px;width:912px;height:1px;background:rgba(255,255,255,.2)}
.hero-title{left:145px;top:226px;width:460px;font-size:28px;line-height:36px;color:var(--white);letter-spacing:3px;white-space:nowrap}
.hero-sub{left:145px;top:376px;width:440px;font-size:13.5px;line-height:24px;color:var(--white)}
.play{left:785px;top:300px;width:90px;height:90px;border-radius:50%;background:rgba(26,163,232,.35);display:flex;align-items:center;justify-content:center}
.play-inner{width:70px;height:70px;border-radius:50%;background:var(--accent);display:flex;align-items:center;justify-content:center}
.dots .dot{position:absolute;left:1121px;width:12px;height:12px;border-radius:50%;background:#7c8596}
.dots .dot.active{left:1116px;width:22px;height:22px;background:var(--blue);border:5px solid #1e8fd6}

/* about */
.about-title{left:145px;top:780px;font-size:37px;line-height:44px}
.about-text{left:144px;top:838px;width:912px;font-size:13.5px;line-height:24px;color:var(--text);text-align:justify}

/* partners */
.section-title{left:0;width:1200px;text-align:center;font-size:37px;line-height:57px}
.partner-band{left:0;top:1310px;width:1200px;height:232px;background:var(--blue-mist)}
.partner-card{position:absolute;top:1310px;height:232px;display:flex;align-items:center;justify-content:center;background:#eff8fd;box-shadow:0 6px 14px rgba(120,160,200,.12)}
.partner-name{font-size:34px;font-weight:700;color:#1b1f2a;letter-spacing:-1px}
.partner-feature{left:292px;top:1296px;width:332px;height:258px;background:var(--white);border:2px solid var(--accent)}
.partner-photo{position:absolute;left:17px;top:0;width:292px;height:176px;background:linear-gradient(180deg,#5f6570 0%,#8c8680 45%,#5a4b42 100%)}
.partner-feature .partner-name{position:absolute;left:0;top:196px;width:100%;text-align:center;font-size:30px;font-weight:400;color:#333;letter-spacing:1px}

/* customers */
.world{left:165px;top:1752px;width:870px;height:490px;background:radial-gradient(ellipse 50% 50% at 50% 50%,#eef2f7 0%,#f7f9fc 60%,#ffffff 100%)}
.client{position:absolute;width:88px;height:88px;margin:-44px 0 0 -44px;border-radius:50%;background:var(--white);box-shadow:0 6px 16px rgba(60,90,140,.16);display:flex;align-items:center;justify-content:center;text-align:center;font-size:12px;font-weight:600;color:#333;line-height:14px}

/* sectors */
.sector{position:absolute;top:2444px;height:388px}
.sector-label{position:absolute;left:33px;bottom:32px;font-size:21px;font-weight:700;color:var(--white)}
.divider{position:absolute;top:2444px;width:7px;height:388px;background:var(--accent)}

/* footer */
.foot-title{top:2914px;font-size:19px;line-height:24px;letter-spacing:3px;white-space:nowrap}
.foot-list{list-style:none;font-size:13.5px;line-height:24px;color:var(--muted)}
.foot-list li{display:flex;align-items:center;gap:12px}
.foot-list svg{flex:none}
.contact-list li{align-items:flex-start}
.contact-list li svg{margin-top:6px}
.email-field{left:768px;top:2958px;width:288px;height:35px;border:1px solid #dde2e8;display:flex;align-items:center;gap:10px;padding-left:14px;font-size:13.5px;color:var(--muted)}
.foot-rule{left:144px;top:3119px;width:912px;height:1px;background:#d9dde3}
.copyright{left:0;top:3154px;width:1200px;text-align:center;font-size:13px;color:var(--muted)}
.copyright span{color:var(--accent)}
</style>
</head>
<body>

<!-- hero -->
<div class="abs hero" role="img" aria-label="Dark blue digital scene of glowing data streams over a circuit landscape"></div>
<div class="abs hero-glow"></div>

<div class="abs brand">
  <div class="brand-name">Corveth Systems</div>
</div>
<nav class="abs nav">
  <span>Robotics and Automation Solutions</span>
  <span>About</span>
  <span>Contact</span>
</nav>
<div class="abs social"></div>
<div class="abs header-rule"></div>

<h1 class="abs display hero-title">Your Automation,<br>IT and Data<br>Centre Solutions<br>Provider</h1>
<p class="abs hero-sub">A Pelmont Controls Distributor Specialising in Life Sciences and Data Centres.</p>
<div class="btn" style="left:145px;top:439px;width:136px;height:39px">Contact Us</div>

<div class="abs play">
  <div class="play-inner">
    <svg width="18" height="20" viewBox="0 0 18 20"><path d="M2 1 L17 10 L2 19 Z" fill="#fff"/></svg>
  </div>
</div>
<div class="dots">
  <div class="dot active" style="top:262px"></div>
  <div class="dot" style="top:323px"></div>
  <div class="dot" style="top:379px"></div>
  <div class="dot" style="top:435px"></div>
</div>

<!-- about -->
<h2 class="abs display about-title">About Us</h2>
<p class="abs about-text">Corveth Systems provides a wide range of automation and IT solutions used in manufacturing operations. &nbsp;Our solutions span a broad spectrum of technology from physical machines and robots to cloud based management solutions for these systems. Along with Pelmont Controls, we work closely to keep track of supply trends and invest wisely to prepare for customers' future DC projects. We have a large team of specialist technical people spanning the breadth of skills to be able to deploy and support these technologies. Authorised Distributor for Pelmont Controls (Arlen Brook and Safemark are Pelmont Controls brands) Tavrin Robotics Solutions' official distributor</p>
<div class="btn" style="left:145px;top:1000px;width:136px;height:39px">Read More</div>

<!-- partners -->
<h2 class="abs display section-title" style="top:1163px">Corveth Technology<br>Partners</h2>
<div class="abs partner-band"></div>
<div class="partner-card" style="left:0;width:287px"><span class="partner-name">Veloprax</span></div>
<div class="partner-card" style="left:624px;width:272px"><span class="partner-name" style="font-size:28px;color:var(--blue-deep)">Tavrin</span></div>
<div class="partner-card" style="left:900px;width:300px">
  <div style="width:170px;height:50px;border-radius:25px;background:#c9d3dd"></div>
</div>
<div class="abs partner-feature">
  <div class="partner-photo" role="img" aria-label="Photo of a busy trade show hall with exhibition stands"></div>
  <span class="partner-name">Quorelle</span>
</div>

<!-- customers -->
<h2 class="abs display section-title" style="top:1664px">Our Customers</h2>
<div class="abs world" role="img" aria-label="Dotted world map showing customer locations"></div>
<div class="client" style="left:320px;top:1837px">Alvira</div>
<div class="client" style="left:581px;top:1898px;font-size:10px">Brenholt<br>Pharma</div>
<div class="client" style="left:727px;top:1868px">Fizzaro</div>
<div class="client" style="left:858px;top:1837px">Macrosys</div>
<div class="client" style="left:958px;top:1948px">Medvane</div>
<div class="client" style="left:322px;top:1985px">Amberly</div>
<div class="client" style="left:799px;top:1985px">Intaro</div>
<div class="client" style="left:544px;top:2053px">Astrelle</div>
<div class="client" style="left:682px;top:2029px">Dravelo</div>
<div class="client" style="left:415px;top:2098px">Pomelo</div>
<div class="client" style="left:713px;top:2151px">GKL</div>
<div class="client" style="left:889px;top:2116px">Mondaro</div>

<!-- sectors -->
<h2 class="abs display section-title" style="top:2344px">Sectors We Operate In</h2>
<div class="sector" style="left:0;width:392px;background:linear-gradient(160deg,#2b3440 0%,#151b24 60%,#0d1118 100%)" role="img" aria-label="Photo of a scientist working on a tablet in a dim lab">
  <span class="sector-label">Life Sciences</span>
</div>
<div class="divider" style="left:392px"></div>
<div class="sector" style="left:399px;width:392px;background:linear-gradient(180deg,#6b5248 0%,#4e5a5e 45%,#2a2d31 100%)" role="img" aria-label="Photo of a small delivery robot on a street">
  <span class="sector-label">Food &amp; Bev</span>
</div>
<div class="divider" style="left:791px;width:8px"></div>
<div class="sector" style="left:799px;width:401px;background:linear-gradient(160deg,#1e3a66 0%,#15284a 50%,#0b1530 100%)" role="img" aria-label="Photo of an engineer with a laptop in a data centre aisle">
  <span class="sector-label">Data Centres</span>
</div>

<!-- footer -->
<h3 class="abs display foot-title" style="left:143px">Quick Links</h3>
<h3 class="abs display foot-title" style="left:454px">Contact Us</h3>
<h3 class="abs display foot-title" style="left:768px">Newsletter</h3>

<ul class="abs foot-list" style="left:143px;top:2964px">
  <li><svg width="9" height="9" viewBox="0 0 9 9"><path d="M1 1l3 3.5L1 8M5 1l3 3.5L5 8" stroke="#1aa3e8" stroke-width="1.3" fill="none"/></svg>Home</li>
  <li><svg width="9" height="9" viewBox="0 0 9 9"><path d="M1 1l3 3.5L1 8M5 1l3 3.5L5 8" stroke="#1aa3e8" stroke-width="1.3" fill="none"/></svg>About Us</li>
  <li><svg width="9" height="9" viewBox="0 0 9 9"><path d="M1 1l3 3.5L1 8M5 1l3 3.5L5 8" stroke="#1aa3e8" stroke-width="1.3" fill="none"/></svg>Automation Solutions</li>
  <li><svg width="9" height="9" viewBox="0 0 9 9"><path d="M1 1l3 3.5L1 8M5 1l3 3.5L5 8" stroke="#1aa3e8" stroke-width="1.3" fill="none"/></svg>Data Centers</li>
  <li><svg width="9" height="9" viewBox="0 0 9 9"><path d="M1 1l3 3.5L1 8M5 1l3 3.5L5 8" stroke="#1aa3e8" stroke-width="1.3" fill="none"/></svg>Contact</li>
</ul>

<ul class="abs foot-list contact-list" style="left:454px;top:2964px">
  <li><svg width="10" height="12" viewBox="0 0 10 12"><path d="M5 0a4.5 4.5 0 0 0-4.5 4.5C.5 8 5 12 5 12s4.5-4 4.5-7.5A4.5 4.5 0 0 0 5 0zm0 6.3a1.8 1.8 0 1 1 0-3.6 1.8 1.8 0 0 1 0 3.6z" fill="#1aa3e8"/></svg><span>Calder House,<br>Meadow Business Park,<br>Ardmore, Co. Dublin</span></li>
  <li><svg width="11" height="11" viewBox="0 0 11 11"><path d="M2.2 0.5l1.8 2.3-1 1.2c.7 1.5 1.8 2.6 3.3 3.3l1.2-1 2.3 1.8-1 2.2C4.8 10 1 6.2.2 2z" fill="#1aa3e8"/></svg>+353 1 555 0142</li>
  <li><svg width="12" height="10" viewBox="0 0 12 10"><rect x="0" y="1" width="12" height="8.5" rx="1" fill="#1aa3e8"/><path d="M0.5 1.5l5.5 4 5.5-4" stroke="#fff" stroke-width="1.1" fill="none"/></svg>sales@corvethsystems.example</li>
</ul>

<div class="abs email-field">
  <svg width="13" height="10" viewBox="0 0 12 10"><rect x="0" y="1" width="12" height="8.5" rx="1" fill="#1aa3e8"/><path d="M0.5 1.5l5.5 4 5.5-4" stroke="#fff" stroke-width="1.1" fill="none"/></svg>
  Email address
</div>
<div class="btn" style="left:769px;top:3006px;width:95px;height:35px;font-size:12px;border-radius:0">Submit</div>

<div class="abs foot-rule"></div>
<p class="abs copyright">© 2024 Copyright - <span>Company Name</span> &nbsp;| All Rights Reserved</p>

</body>
</html>
```